Looking for a modern, Professional business card design

We have a simple business card, but are looking for a more modern, professional look. A sample of the basic card is attached as well as the logo. We would also like to add that we offer:
Struggling with your finances?
- Learn to become debt free
- Discover the power of cash
- Control your money instead of it controlling you
Let us help you achieve a new level of financial freedom!
Also, we would like to have a "SPECIAL OFFER!: FREE 30 minute consultation"
Financial Planning

```html
<!DOCTYPE html>
<html lang="en">
<head>
<meta charset="utf-8">
<title>Clearway Money Coaching – Business Card</title>
<link href="https://fonts.googleapis.com/css2?family=Source+Sans+3:ital,wght@0,400;0,600;0,700;1,600&display=swap" rel="stylesheet">
<style>
  :root {
    --stage: #000000;
    --card: #2f3032;
    --card-edge: #3a3b3d;
    --green: #7cc242;
    --green-deep: #4fa632;
    --ink: #f2f2f2;
  }
  * { box-sizing: border-box; margin: 0; padding: 0; }
  html, body { width: 1200px; height: 900px; overflow: hidden; background: var(--stage); }
  body { position: relative; font-family: "Source Sans 3", sans-serif; color: var(--ink); }

  .card {
    position: absolute; top: 271px; width: 457px; height: 281px;
    background: radial-gradient(ellipse at 40% 30%, #343537 0%, var(--card) 70%);
    border: 1px solid var(--card-edge);
    border-radius: 14px;
  }
  .card--front { left: 137px; }
  .card--back { left: 626px; }

  .brand { position: absolute; left: 30px; top: 50px; display: flex; align-items: center; gap: 10px; }
  .brand__dot { width: 26px; height: 26px; border-radius: 50%; background: var(--green); }
  .brand__name { font-size: 24px; font-weight: 700; color: var(--green); letter-spacing: 0.3px; }

  .person { position: absolute; left: 233px; top: 145px; }
  .person__name { font-size: 17px; font-weight: 600; color: var(--green); line-height: 20px; }
  .person__title { font-size: 13px; color: var(--ink); line-height: 16px; }

  .contacts { position: absolute; left: 233px; top: 199px; list-style: none; }
  .contacts li { display: flex; align-items: center; gap: 6px; font-size: 13px; line-height: 18px; }
  .contacts svg { width: 10px; height: 10px; flex: none; }

  .offer { position: absolute; left: 30px; top: 27px; font-size: 19.5px; font-weight: 600; white-space: nowrap; }
  .offer__flag { color: var(--green); }

  .mark { position: absolute; left: 62px; top: 95px; width: 120px; display: flex; flex-direction: column; align-items: center; gap: 8px; }
  .mark__dot { width: 62px; height: 62px; border-radius: 50%; background: linear-gradient(160deg, var(--green), var(--green-deep)); }
  .mark__name { font-size: 13px; font-weight: 600; color: var(--green); text-align: center; line-height: 15px; }

  .pitch { position: absolute; left: 212px; top: 92px; }
  .pitch__question { font-size: 14.5px; font-weight: 600; color: var(--green); margin-bottom: 7px; }
  .pitch__list { list-style: none; }
  .pitch__list li { position: relative; padding-left: 22px; font-size: 13.5px; line-height: 19px; }
  .pitch__list svg { position: absolute; left: 4px; top: 4px; width: 14px; height: 11px; }

  .closing { position: absolute; left: 0; right: 0; top: 240px; text-align: center; font-size: 13.5px; font-style: italic; font-weight: 600; color: var(--green); }
</style>
</head>
<body>
  <section class="card card--front">
    <div class="brand">
      <span class="brand__dot"></span>
      <span class="brand__name">Clearway Money Coaching</span>
    </div>
    <div class="person">
      <p class="person__name">Daniel R. Hayes</p>
      <p class="person__title">Personal Financial Coach</p>
    </div>
    <ul class="contacts">
      <li><svg viewBox="0 0 10 10"><path d="M2 1l2 2-1 1.3c.6 1.2 1.5 2.1 2.7 2.7L7 6l2 2-1.3 1.3C4.5 9 1 5.5.7 2.3z" fill="#7cc242"/></svg>(555) 013-2748</li>
      <li><svg viewBox="0 0 10 10"><rect x="0.5" y="2" width="9" height="6.5" fill="#7cc242"/><path d="M0.5 2L5 5.5 9.5 2" stroke="#2f3032" stroke-width="1" fill="none"/></svg>daniel@clearwaymoney.com</li>
      <li><svg viewBox="0 0 10 10"><circle cx="5" cy="5" r="4.5" fill="#7cc242"/><path d="M.5 5h9M5 .5c-2 2.5-2 6.5 0 9M5 .5c2 2.5 2 6.5 0 9" stroke="#2f3032" stroke-width=".8" fill="none"/></svg>www.clearwaymoney.com</li>
    </ul>
  </section>

  <section class="card card--back">
    <p class="offer"><span class="offer__flag">SPECIAL OFFER!</span> FREE 30 minute &nbsp;consultation</p>
    <div class="mark">
      <span class="mark__dot"></span>
      <span class="mark__name">Clearway Money Coaching</span>
    </div>
    <div class="pitch">
      <p class="pitch__question">Struggling with your finances?</p>
      <ul class="pitch__list">
        <li><svg viewBox="0 0 14 11"><path d="M1 6l4 4 8-9" stroke="#7cc242" stroke-width="2.4" fill="none"/></svg>Learn to become debt free</li>
        <li><svg viewBox="0 0 14 11"><path d="M1 6l4 4 8-9" stroke="#7cc242" stroke-width="2.4" fill="none"/></svg>Discover the power of cash</li>
        <li><svg viewBox="0 0 14 11"><path d="M1 6l4 4 8-9" stroke="#7cc242" stroke-width="2.4" fill="none"/></svg>Control your money<br>instead of it &nbsp;controlling you</li>
      </ul>
    </div>
    <p class="closing">Let us help you achieve a new &nbsp;level of &nbsp;financial freedom!</p>
  </section>
</body>
</html>
```